Card design for orthopaedic surgeons working as The Brightwater Joint Centre

Business cards, letterhead

Colors

Designer to choose colors to be used in the design.

Requirements
Must have
• Late addition.
• Cards letterhead must have logos of
• Crestmoor Lindell College of Surgeons
• Varenwood Bone Health Association
Nice to have
• Back of card to have space for appointment time to be added by hand and some blank space for writing incidental other notes.

```html
<!DOCTYPE html>
<html lang="en">
<head>
<meta charset="utf-8">
<title>The Brightwater Joint Centre – Business Cards</title>
<link href="https://fonts.googleapis.com/css2?family=Montserrat:wght@400&family=Open+Sans:wght@400;600&family=Arimo:wght@700&display=swap" rel="stylesheet">
<style>
  :root {
    --bg: #d9dadb;
    --card: #ffffff;
    --sky: #33b1f5;
    --navy: #0b3350;
    --ink: #222a30;
    --white: #ffffff;
    --badge: #e3ecf2;
    --badge-edge: #b9cbd8;
  }
  * { margin: 0; padding: 0; box-sizing: border-box; }
  html, body { width: 1200px; height: 1200px; overflow: hidden; }
  body {
    background: var(--bg);
    font-family: "Open Sans", sans-serif;
    position: relative;
  }
  .card {
    position: absolute;
    left: 180px;
    width: 840px;
    height: 480px;
    background: var(--card);
    border-radius: 36px;
    overflow: hidden;
    box-shadow: 0 6px 18px rgba(0,0,0,0.18);
  }
  .card--back { top: 80px; }
  .card--front { top: 640px; }

  .wordmark {
    font-family: "Montserrat", sans-serif;
    font-weight: 400;
    color: var(--navy);
    letter-spacing: -0.5px;
    white-space: nowrap;
  }
  .card--back .wordmark {
    position: absolute;
    top: 156px;
    left: 0; right: 0;
    text-align: center;
    font-size: 44px;
  }
  .card--back .website {
    position: absolute;
    top: 242px;
    left: 0; right: 0;
    text-align: center;
    font-size: 21px;
    letter-spacing: 6px;
    color: var(--ink);
  }
  .affiliations {
    position: absolute;
    top: 340px;
    left: 0; right: 0;
    display: flex;
    justify-content: center;
    gap: 40px;
  }
  .affiliation-badge {
    width: 72px;
    height: 72px;
    border-radius: 50%;
    background: var(--badge);
    border: 2px solid var(--badge-edge);
  }

  .front-art { position: absolute; inset: 0; }
  .card--front .wordmark {
    position: absolute;
    top: 70px;
    left: 0; right: 0;
    padding-left: 80px;
    text-align: center;
    font-size: 40px;
  }
  .person {
    position: absolute;
    top: 176px;
    left: 340px;
    width: 340px;
    text-align: center;
  }
  .person__name {
    font-family: "Arimo", sans-serif;
    font-weight: 700;
    font-size: 26px;
    color: var(--navy);
  }
  .person__title {
    font-size: 21px;
    color: var(--sky);
    line-height: 1.1;
  }
  .contact {
    position: absolute;
    color: var(--white);
    font-size: 19px;
    display: flex;
    align-items: center;
    gap: 10px;
    white-space: nowrap;
  }
  .contact svg { width: 18px; height: 18px; flex: none; }
  .contact--email { top: 292px; left: 40px; }
  .contact--phone { top: 330px; left: 330px; }
  .contact--address { top: 392px; left: 60px; }
  .contact--web { top: 392px; left: 450px; }
</style>
</head>
<body>

<section class="card card--back" aria-label="Card back">
  <p class="wordmark">The Brightwater Joint Centre</p>
  <p class="website">www.brightwaterjoint.com</p>
  <div class="affiliations">
    <div class="affiliation-badge" role="img" aria-label="Crestmoor Lindell College of Surgeons membership badge"></div>
    <div class="affiliation-badge" role="img" aria-label="Varenwood Bone Health Association membership badge"></div>
  </div>
</section>

<section class="card card--front" aria-label="Card front">
  <svg class="front-art" viewBox="0 0 840 480" preserveAspectRatio="none" aria-hidden="true">
    <path d="M0,150 C200,260 480,360 840,352 L840,480 L0,480 Z" fill="var(--sky)"/>
    <path d="M0,110 C190,230 430,330 690,348 C430,336 190,250 0,140 Z" fill="var(--navy)"/>
  </svg>

  <p class="wordmark">The Brightwater Joint Centre</p>

  <div class="person">
    <p class="person__name">Miriam Hollis</p>
    <p class="person__title">Title</p>
  </div>

  <p class="contact contact--email">
    <svg viewBox="0 0 20 20"><rect x="1" y="4" width="18" height="12" rx="1.5" fill="none" stroke="currentColor" stroke-width="2"/><path d="M2,5 L10,11 L18,5" fill="none" stroke="currentColor" stroke-width="2"/></svg>
    info@brightwaterjoint.com
  </p>
  <p class="contact contact--phone">
    <svg viewBox="0 0 20 20"><path d="M5,2 L8,2 L9,6 L7,8 C8,10.5 9.5,12 12,13 L14,11 L18,12 L18,15 C18,17 16.5,18 15,18 C8,17.5 2.5,12 2,5 C2,3.5 3,2 5,2 Z" fill="currentColor"/></svg>
    012-345-6789
  </p>
  <p class="contact contact--address">Street Name, City Name, Zipcode - 012345</p>
  <p class="contact contact--web">
    <svg viewBox="0 0 20 20"><g fill="none" stroke="currentColor" stroke-width="1.6"><circle cx="10" cy="10" r="8"/><ellipse cx="10" cy="10" rx="3.5" ry="8"/><path d="M2,10 H18 M3.5,6 H16.5 M3.5,14 H16.5"/></g></svg>
    www.brightwaterjoint.com
  </p>
</section>

</body>
</html>
```